FinTech company looking to revamp and expand client-facing interface for our financial models

Pellworth Engines currently has a very simple website that allows clients to interact with our financial models. We are looking to completely redesign the current site and add several extra pages to provide extra functionality. We want the design to have a modern, slick feel, that will work on both a desktop or a tablet. It should be straightforward for clients to move between different pages at any time, and clear from the layout how to interact with the more advanced features. We have included screenshots of existing pages in the attached design brief, as well as sketches of the functionality required by the new pages, but can't provide a direct link to the current site.
Target Market(s)
Professional investors that will be paying to access the interface
Industry/Entity Type
Finance
Number of Pages Required
4 page
Colors
Designer to choose colors to be used in the design.
Look and feel
Each slider illustrates characteristics of the customer's brand and the style your logo design should communicate.

```html
<!DOCTYPE html>
<html lang="en">
<head>
<meta charset="utf-8">
<title>Pellworth Engines – Models</title>
<link href="https://fonts.googleapis.com/css2?family=Montserrat:wght@400;500;600;700&display=swap" rel="stylesheet">
<style>
:root{
  --bg:#e9eff5;
  --blue:#1f80d8;
  --blue-2:#2d8fe2;
  --white:#ffffff;
  --ink:#2a2f36;
  --muted:#8d9cae;
  --placeholder:#b3bdc9;
  --row-alt:#f5f8fc;
  --line:#c9d1da;
  --accent:#2b86d9;
  --green:#3cb64a;
  --red:#f0474a;
}
*{box-sizing:border-box;margin:0;padding:0}
html,body{width:1200px;height:772px;overflow:hidden}
body{background:var(--bg);font-family:'Montserrat',sans-serif;color:var(--ink);position:relative}
.topbar{position:absolute;left:0;top:0;width:1200px;height:67px;background:linear-gradient(90deg,var(--blue),var(--blue-2));box-shadow:0 2px 8px rgba(30,90,150,.15);color:var(--white)}
.brand{position:absolute;left:150px;top:19px;font-size:23px;font-weight:700;letter-spacing:.5px}
.horizon{position:absolute;top:26px;font-size:12.5px;font-weight:500}
.horizon.active{opacity:.75}
.horizon.active::after{content:"";position:absolute;left:-8px;right:-9px;top:38px;height:2px;background:rgba(255,255,255,.35)}
.nav{position:absolute;top:25px;font-size:12.5px;font-weight:500;display:flex;align-items:center;gap:6px}
.nav svg{width:14px;height:14px}
.nav.active{opacity:.75}
.nav.active::after{content:"";position:absolute;left:-6px;right:-9px;top:39px;height:2px;background:rgba(255,255,255,.35)}
.card{position:absolute;left:150px;width:900px;background:var(--white);border-radius:3px}
.tabs{top:118px;height:52px}
.tab{position:absolute;top:20px;font-size:11px;font-weight:500;letter-spacing:.3px}
.tab.active{color:var(--accent)}
.tab.active::after{content:"";position:absolute;left:-7px;right:-8px;top:30px;height:2px;background:var(--accent)}
.tab.add{color:#9cc4ea;font-size:12px;top:18px}
.divider{position:absolute;top:15px;height:22px;border-left:1px dashed #bfd8ef}
.filters{top:189px;height:52px}
.flabel{position:absolute;top:20px;font-size:11px;font-weight:500}
.ph{position:absolute;top:20px;font-size:11px;color:var(--placeholder)}
.uline{position:absolute;top:51px;height:1px;background:var(--line)}
.icon{position:absolute}
.apply{position:absolute;left:814px;top:3px;width:83px;height:46px;background:var(--green);color:var(--white);border-radius:2px;font-size:12.5px;font-weight:500;display:flex;align-items:center;justify-content:center;gap:6px}
.grid{top:260px;height:464px;overflow:hidden}
.row{display:grid;grid-template-columns:92px 83px 88px 78px 69px 68px 75px 72px 71px 70px 67px 1fr;padding-left:10px;align-items:center;font-size:13px}
.head{height:45px;background:var(--row-alt);color:var(--muted);font-weight:500}
.head span:first-child{padding-left:4px}
.body-row{height:70px}
.body-row:nth-child(odd){background:var(--row-alt)}
.idcell{display:flex;align-items:center;gap:6px}
.idcell svg{width:10px;height:10px}
.time{font-size:12.5px;line-height:16px}
.num{font-size:12.5px}
</style>
</head>
<body>
<header class="topbar">
  <div class="brand">KARVO</div>
  <span class="horizon active" style="left:276px">250D</span>
  <span class="horizon" style="left:340px">83D</span>
  <span class="horizon" style="left:397px">42D</span>
  <span class="nav active" style="left:555px"><svg viewBox="0 0 16 16" fill="none" stroke="#fff" stroke-width="1.4"><path d="M2 7.5 8 2l6 5.5V14H2z"/></svg>Models</span>
  <span class="nav" style="left:661px"><svg viewBox="0 0 16 16" fill="none" stroke="#fff" stroke-width="1.3"><circle cx="3" cy="3" r="1.4"/><circle cx="8" cy="3" r="1.4"/><circle cx="13" cy="3" r="1.4"/><circle cx="3" cy="8" r="1.4"/><circle cx="8" cy="8" r="1.4"/><circle cx="13" cy="8" r="1.4"/><circle cx="3" cy="13" r="1.4"/><circle cx="8" cy="13" r="1.4"/></svg>Portfolio Builder</span>
  <span class="nav" style="left:820px"><svg viewBox="0 0 16 16" fill="none" stroke="#fff" stroke-width="1.4"><path d="M8 2 15 6 8 10 1 6z"/><path d="M1 9.5 8 13.5 15 9.5"/></svg>Sensitivities</span>
  <span class="nav" style="left:958px"><svg viewBox="0 0 16 16" fill="none" stroke="#fff" stroke-width="1.4"><path d="M8 1.5l2 4.3 4.6.5-3.4 3.1 1 4.6L8 11.7 3.8 14l1-4.6L1.4 6.3 6 5.8z"/></svg>Favourites</span>
</header>

<section class="card tabs">
  <span class="tab active" style="left:26px">EQUITIES</span>
  <span class="divider" style="left:101px"></span>
  <span class="tab" style="left:123px">ETFS</span>
  <span class="divider" style="left:174px"></span>
  <span class="tab" style="left:193px">PAIRS</span>
  <span class="divider" style="left:249px"></span>
  <span class="tab" style="left:270px">ETF PAIRS</span>
  <span class="divider" style="left:351px"></span>
  <span class="tab" style="left:371px">FACTORS</span>
  <span class="tab add" style="left:447px">+ Add</span>
</section>

<section class="card filters">
  <svg class="icon" style="left:16px;top:21px" width="10" height="10" viewBox="0 0 10 10" stroke="var(--red)" stroke-width="1.4"><path d="M1 1l8 8M9 1l-8 8"/></svg>
  <span class="flabel" style="left:50px">Sector:</span>
  <span class="ph" style="left:103px">Materials</span>
  <svg class="icon" style="left:222px;top:24px" width="10" height="6" viewBox="0 0 10 6" fill="none" stroke="#7d8896" stroke-width="1.2"><path d="M1 1l4 4 4-4"/></svg>
  <span class="uline" style="left:105px;width:127px"></span>
  <span class="flabel" style="left:254px">Time:</span>
  <span class="ph" style="left:298px">From</span>
  <svg class="icon" style="left:340px;top:19px" width="14" height="14" viewBox="0 0 14 14" fill="none" stroke="#9aa6b3" stroke-width="1.1"><rect x="1" y="2.5" width="12" height="10.5" rx="1"/><path d="M1 6h12M4 1v3M10 1v3"/></svg>
  <span class="ph" style="left:367px">To</span>
  <svg class="icon" style="left:389px;top:19px" width="14" height="14" viewBox="0 0 14 14" fill="none" stroke="#9aa6b3" stroke-width="1.1"><rect x="1" y="2.5" width="12" height="10.5" rx="1"/><path d="M1 6h12M4 1v3M10 1v3"/></svg>
  <span class="flabel" style="left:425px">Quality:</span>
  <span class="ph" style="left:482px">From</span>
  <span class="uline" style="left:484px;width:52px"></span>
  <span class="ph" style="left:552px">To</span>
  <span class="uline" style="left:552px;width:52px"></span>
  <span class="flabel" style="left:625px">Stat:</span>
  <span class="ph" style="left:664px">From</span>
  <span class="uline" style="left:666px;width:52px"></span>
  <span class="ph" style="left:734px">To</span>
  <span class="uline" style="left:733px;width:53px"></span>
  <div class="apply"><svg width="13" height="10" viewBox="0 0 13 10" fill="none" stroke="#fff" stroke-width="1.5"><path d="M1 5l4 4 7-8"/></svg>Apply</div>
</section>

<section class="card grid">
  <div class="row head">
    <span>ID ⌄</span><span>Sector</span><span>Time</span><span>Quality</span><span>Stat 1</span><span>Stat 2</span><span>Stat 3</span><span>Stat 4</span><span>Stat 5</span><span>Stat 6</span><span>Stat 7</span><span>Stat 8</span>
  </div>
  <div class="rows">
    <div class="row body-row"><span class="idcell"><svg viewBox="0 0 16 16" fill="none" stroke="#b7c0cb" stroke-width="1.2"><path d="M8 1.5l2 4.3 4.6.5-3.4 3.1 1 4.6L8 11.7 3.8 14l1-4.6L1.4 6.3 6 5.8z"/></svg>Model 1</span><span>Materials</span><span class="time">2019-07-03<br>12:15:00.000</span><span class="num">30.2888</span><span class="num">2.01574</span><span class="num">23.305</span><span class="num">-0.149368</span><span class="num">22.3054</span><span class="num">4.63714</span><span class="num">0.945706</span><span class="num">2.81949</span><span class="num">2.60858</span></div>
    <div class="row body-row"><span class="idcell"><svg viewBox="0 0 16 16" fill="var(--red)"><path d="M8 1.5l2 4.3 4.6.5-3.4 3.1 1 4.6L8 11.7 3.8 14l1-4.6L1.4 6.3 6 5.8z"/></svg>Model 2</span><span>Materials</span><span class="time">2019-07-03<br>12:15:00.000</span><span class="num">30.2888</span><span class="num">2.01574</span><span class="num">23.305</span><span class="num">-0.149368</span><span class="num">22.3054</span><span class="num">4.63714</span><span class="num">0.945706</span><span class="num">2.81949</span><span class="num">2.60858</span></div>
    <div class="row body-row"><span class="idcell"><svg viewBox="0 0 16 16" fill="none" stroke="#b7c0cb" stroke-width="1.2"><path d="M8 1.5l2 4.3 4.6.5-3.4 3.1 1 4.6L8 11.7 3.8 14l1-4.6L1.4 6.3 6 5.8z"/></svg>Model 3</span><span>Materials</span><span class="time">2019-07-03<br>12:15:00.000</span><span class="num">30.2888</span><span class="num">2.01574</span><span class="num">23.305</span><span class="num">-0.149368</span><span class="num">22.3054</span><span class="num">4.63714</span><span class="num">0.945706</span><span class="num">2.81949</span><span class="num">2.60858</span></div>
    <div class="row body-row"><span class="idcell"><svg viewBox="0 0 16 16" fill="none" stroke="#b7c0cb" stroke-width="1.2"><path d="M8 1.5l2 4.3 4.6.5-3.4 3.1 1 4.6L8 11.7 3.8 14l1-4.6L1.4 6.3 6 5.8z"/></svg>Model 4</span><span>Materials</span><span class="time">2019-07-03<br>12:15:00.000</span><span class="num">30.2888</span><span class="num">2.01574</span><span class="num">23.305</span><span class="num">-0.149368</span><span class="num">22.3054</span><span class="num">4.63714</span><span class="num">0.945706</span><span class="num">2.81949</span><span class="num">2.60858</span></div>
    <div class="row body-row"><span class="idcell"><svg viewBox="0 0 16 16" fill="none" stroke="#b7c0cb" stroke-width="1.2"><path d="M8 1.5l2 4.3 4.6.5-3.4 3.1 1 4.6L8 11.7 3.8 14l1-4.6L1.4 6.3 6 5.8z"/></svg>Model 5</span><span>Materials</span><span class="time">2019-07-03<br>12:15:00.000</span><span class="num">30.2888</span><span class="num">2.01574</span><span class="num">23.305</span><span class="num">-0.149368</span><span class="num">22.3054</span><span class="num">4.63714</span><span class="num">0.945706</span><span class="num">2.81949</span><span class="num">2.60858</span></div>
    <div class="row body-row"><span class="idcell"><svg viewBox="0 0 16 16" fill="none" stroke="#b7c0cb" stroke-width="1.2"><path d="M8 1.5l2 4.3 4.6.5-3.4 3.1 1 4.6L8 11.7 3.8 14l1-4.6L1.4 6.3 6 5.8z"/></svg>Model 6</span><span>Materials</span><span class="time">2019-07-03<br>12:15:00.000</span><span class="num">30.2888</span><span class="num">2.01574</span><span class="num">23.305</span><span class="num">-0.149368</span><span class="num">22.3054</span><span class="num">4.63714</span><span class="num">0.945706</span><span class="num">2.81949</span><span class="num">2.60858</span></div>
  </div>
</section>
</body>
</html>
```